Website Quibrel Outdoor

Hi I'm looking for a simple design for a new website. It's outdoor products mainly in category, Boat, Tarpaulin, Fishing, Golf. I have include image and text for 8 products + presentation etc. I want a simple and modern site + fast + Mobile. Wordpress. I'm going to sell through Tradovik so I don't need any WooCommerce but a buy button to Tradovik. I haven set up the Tradovik account yet. My logo i s grey and orange. My goal is to sell in Tradovik US and later EU.

```html
<!DOCTYPE html>
<html lang="en">
<head>
<meta charset="utf-8">
<title>Quibrel Outdoor</title>
<link rel="stylesheet" href="https://fonts.googleapis.com/css2?family=Roboto:wght@400;500;700;900&display=swap">
<style>
:root{
  --orange:#ff7f00;
  --ink:#222222;
  --light:#f5f5f5;
  --white:#ffffff;
  --black:#000000;
  --grey:#5f5f5f;
}
*{box-sizing:border-box;margin:0;padding:0}
html,body{width:1200px;height:3289px;overflow:hidden}
body{font-family:'Roboto',sans-serif;color:var(--ink);background:var(--white);position:relative}
a{color:inherit;text-decoration:none}

/* hero */
.hero{position:absolute;left:0;top:0;width:1200px;height:600px;
  background:linear-gradient(120deg,#2e3324 0%,#4a4630 30%,#8a5228 52%,#5a3a22 70%,#242a1e 100%)}
.hero-shade{position:absolute;inset:0;background:radial-gradient(ellipse at 50% 45%,rgba(0,0,0,.05),rgba(0,0,0,.35))}
.topline{position:absolute;top:14px;left:152px;display:flex;align-items:center;gap:8px;color:var(--white)}
.round{width:32px;height:32px;border-radius:50%;background:var(--orange);display:flex;align-items:center;justify-content:center}
.topline .label{font-size:13px;font-weight:700}
.topline .num{font-size:20px;font-weight:700}
.social{position:absolute;display:flex;gap:14px}
.social .dot{width:30px;height:30px;border-radius:50%;background:var(--orange);display:flex;align-items:center;justify-content:center}
.social.top{top:16px;left:873px}
.nav{position:absolute;left:132px;top:55px;width:935px;height:61px;background:var(--white);border-radius:10px;
  font-size:14px;font-weight:500;color:#111}
.nav a{position:absolute;top:22px}
.brand-bump{position:absolute;left:535px;top:12px;width:130px;height:100px;border-radius:65px 65px 0 0;background:var(--white)}
.brand{position:absolute;left:500px;top:20px;width:200px;text-align:center;color:var(--orange);font-weight:700;font-size:21px;line-height:22px;letter-spacing:1px}
.brand .mark{display:block;width:36px;height:36px;border-radius:50%;background:var(--grey);margin:0 auto 6px}
.hero h1{position:absolute;top:218px;width:1200px;text-align:center;color:var(--white);font-size:68px;font-weight:700}
.hero p{position:absolute;top:307px;left:150px;width:900px;text-align:center;color:var(--white);font-size:14px;line-height:28px}
.btn{position:absolute;display:flex;align-items:center;justify-content:center;border-radius:26px;font-weight:700;font-size:15px}
.btn.solid{background:var(--orange);color:var(--white)}
.btn.light{background:var(--white);color:var(--orange)}
.dots{position:absolute;top:557px;left:576px;display:flex;gap:4px}
.dots span{width:9px;height:9px;border-radius:50%;background:var(--white)}
.dots span:first-child{background:var(--orange)}

/* section headings */
.heading{position:absolute;width:1200px;text-align:center;font-size:31px;font-weight:700;color:var(--ink)}
.heading::after{content:"";display:block;width:36px;height:3px;background:var(--orange);margin:14px auto 0}

/* products */
.product{position:absolute;top:751px;width:221px;text-align:center}
.product .shot{height:246px;background:#f4f4f4}
.shot.glasses{background:radial-gradient(ellipse 40% 22% at 58% 58%,#d6d6de 0%,#e4e4ea 60%,#f4f4f4 100%),#f4f4f4}
.shot.towel{background:radial-gradient(ellipse 18% 40% at 50% 55%,#7a7a7a 0%,#a8a8a8 55%,#f4f4f4 100%),#f4f4f4}
.shot.tarp{background:radial-gradient(ellipse 42% 38% at 50% 45%,#3a8a4a 0%,#3f8c4e 70%,#f4f4f4 100%),#f4f4f4}
.shot.shelter{background:radial-gradient(ellipse 42% 26% at 45% 45%,#dedede 0%,#e8e8e8 60%,#f4f4f4 100%),#f4f4f4}
.product .name{margin-top:18px;font-size:15px;font-weight:700}
.product .price{margin-top:10px;font-size:13px;color:var(--orange)}
.arrow{position:absolute;top:853px;width:44px;height:44px;border-radius:50%;background:var(--orange);display:flex;align-items:center;justify-content:center}

/* about */
.about-photo{position:absolute;left:0;top:1139px;width:600px;height:475px;
  background:linear-gradient(170deg,#8ea6c7 0%,#d7d9db 35%,#b9bcbf 60%,#3c3a36 100%)}
.about{position:absolute;left:600px;top:1139px;width:600px;height:475px;background:var(--orange);color:var(--white)}
.about h2{position:absolute;left:65px;top:70px;font-size:31px;font-weight:700}
.about h2::after{content:"";display:block;width:34px;height:3px;background:var(--white);margin-top:14px}
.about p{position:absolute;left:65px;top:142px;width:425px;font-size:13px;line-height:28px}

/* blog */
.blog{position:absolute;left:0;top:1614px;width:1200px;height:565px;background:var(--light)}
.post{position:absolute;top:1792px;width:302px}
.post .shot{height:242px}
.post h3{margin:14px 8px 0;font-size:14.5px;font-weight:700;line-height:28px;text-transform:uppercase;color:#333}

/* instagram */
.tile{position:absolute}

/* footer */
.footer{position:absolute;left:0;top:2925px;width:1200px;height:364px;background:var(--black);color:var(--white)}
.footer .brand{top:68px;color:var(--white);font-size:26px;line-height:28px}
.footer .brand .mark{background:var(--white);width:44px;height:44px}
.footlinks{position:absolute;top:192px;width:1200px;display:flex;justify-content:center;gap:34px;font-size:12px;font-weight:500}
.social.bottom{top:228px;left:518px}
.copy{position:absolute;top:282px;width:1200px;text-align:center;font-size:11px;font-weight:500}
</style>
</head>
<body>

<header class="hero">
  <div class="hero-shade" role="img" aria-label="Photo of an angler in an orange jacket holding a fly rod and landing net outdoors"></div>

  <div class="topline">
    <span class="round"><svg width="16" height="16" viewBox="0 0 24 24"><path fill="#fff" d="M6.6 10.8a15 15 0 006.6 6.6l2.2-2.2a1 1 0 011-.25 11.4 11.4 0 003.6.57 1 1 0 011 1V20a1 1 0 01-1 1A17 17 0 013 4a1 1 0 011-1h3.5a1 1 0 011 1 11.4 11.4 0 00.57 3.6 1 1 0 01-.25 1z"/></svg></span>
    <span class="label">CALL US TODAY :</span><span class="num">+123 555 0142</span>
  </div>

  <div class="social top">
    <span class="dot" aria-label="Share"><svg width="14" height="14" viewBox="0 0 24 24"><circle cx="18" cy="5" r="3" fill="#fff"/><circle cx="6" cy="12" r="3" fill="#fff"/><circle cx="18" cy="19" r="3" fill="#fff"/><path d="M8.6 10.5l6.8-4M8.6 13.5l6.8 4" stroke="#fff" stroke-width="2"/></svg></span>
    <span class="dot" aria-label="Email"><svg width="14" height="14" viewBox="0 0 24 24"><rect x="2" y="5" width="20" height="14" rx="2" fill="none" stroke="#fff" stroke-width="2.2"/><path d="M3 6l9 7 9-7" fill="none" stroke="#fff" stroke-width="2.2"/></svg></span>
    <span class="dot" aria-label="Chat"><svg width="14" height="14" viewBox="0 0 24 24"><path d="M4 4h16v11H9l-5 4z" fill="#fff"/></svg></span>
    <span class="dot" aria-label="Cart"><svg width="16" height="16" viewBox="0 0 24 24"><path d="M3 4h3l2 10h10l2-7H8" stroke="#fff" stroke-width="2" fill="none"/><circle cx="10" cy="19" r="1.8" fill="#fff"/><circle cx="17" cy="19" r="1.8" fill="#fff"/></svg></span>
  </div>

  <div class="brand-bump"></div>
  <nav class="nav">
    <a style="left:48px">HOME</a>
    <a style="left:127px">ABOUT US</a>
    <a style="left:233px">SHOP</a>
    <a style="left:608px">REVIEWS</a>
    <a style="left:709px">BLOGS</a>
    <a style="left:792px">CONTACT US</a>
  </nav>
  <div class="brand"><span class="mark"></span>QUIBREL<br>OUTDOOR</div>

  <h1>Welcome To Quibrel Outdoor</h1>
  <p>Lorem ipsum dolor sit amet, consectetur adipiscing elit, sed do eiusmod tempor incididunt ut labore et dolore magna aliqua.<br>Quis ipsum suspendisse ultrices gravida. Risus commodo viverra maecenas accumsan lacus vel facilisis.</p>
  <a class="btn solid" style="left:488px;top:382px;width:225px;height:52px">Shop All Collection</a>
  <div class="dots"><span></span><span></span><span></span><span></span></div>
</header>

<h2 class="heading" style="top:665px">Shop Our Products</h2>

<a class="arrow" style="left:69px"><svg width="14" height="14" viewBox="0 0 24 24"><path d="M15 5l-7 7 7 7" stroke="#fff" stroke-width="3.5" fill="none"/></svg></a>
<article class="product" style="left:132px"><div class="shot glasses" role="img" aria-label="Product photo: floating sunglasses strap"></div><div class="name">Product name</div><div class="price">$ 120:00</div></article>
<article class="product" style="left:370px"><div class="shot towel" role="img" aria-label="Product photo: grey towel with clip"></div><div class="name">Product name</div><div class="price">$ 120:00</div></article>
<article class="product" style="left:608px"><div class="shot tarp" role="img" aria-label="Product photo: green tarpaulin with zipper"></div><div class="name">Product name</div><div class="price">$ 120:00</div></article>
<article class="product" style="left:847px"><div class="shot shelter" role="img" aria-label="Product photo: tarp shelter and bungee hooks"></div><div class="name">Product name</div><div class="price">$ 120:00</div></article>
<a class="arrow" style="left:1087px"><svg width="14" height="14" viewBox="0 0 24 24"><path d="M9 5l7 7-7 7" stroke="#fff" stroke-width="3.5" fill="none"/></svg></a>

<div class="about-photo" role="img" aria-label="Photo of boats covered with tarpaulins in a winter storage yard"></div>
<section class="about">
  <h2>About Us</h2>
  <p>Sed ut perspiciatis unde omnis iste natus error sit voluptatem accusantium doloremque laudantium, totam rem aperiam, eaque ipsa quae ab illo inventore veritatis et quasi architecto beatae vitae dicta sunt explicabo. Nemo enim ipsam voluptatem quia voluptas sit aspernatur aut odit aut fugit, sed quia consequuntur magni dolores eos qui ratione voluptatem sequi nesciunt. Neque porro quisquam est, qui dolorem ipsum quia dolor sit amet.</p>
  <a class="btn light" style="left:65px;top:351px;width:225px;height:51px">Shop Now</a>
</section>

<section class="blog"></section>
<h2 class="heading" style="top:1696px">Our Latest Blog</h2>
<article class="post" style="left:132px"><div class="shot" role="img" aria-label="Photo of a golf bag on a trolley and a player wiping a club" style="background:linear-gradient(160deg,#7d8b6a,#4f7a2c 60%,#6a8d3a)"></div><h3>Lorem ipsum dolor sit amet, cons ectetur adipiscing elit.</h3></article>
<article class="post" style="left:450px"><div class="shot" role="img" aria-label="Photo of a boat cabin door with a safety sign" style="background:linear-gradient(160deg,#cfcfca,#a8a49b 60%,#7a4a2c)"></div><h3>Lorem ipsum dolor sit amet, cons ectetur adipiscing elit.</h3></article>
<article class="post" style="left:766px"><div class="shot" role="img" aria-label="Photo of towels being washed in a washing machine with care tips" style="background:linear-gradient(160deg,#d8d8d6,#8a8e92 55%,#2a5fb0)"></div><h3>Lorem ipsum dolor sit amet, cons ectetur adipiscing elit.</h3></article>

<h2 class="heading" style="top:2264px">Follow Us To Instagram</h2>
<div class="tile" style="left:132px;top:2355px;width:227px;height:309px;background:linear-gradient(160deg,#dfe3e8,#8fa5c8 50%,#2b5cc4)" role="img" aria-label="Instagram photo: tarpaulin detail"></div>
<div class="tile" style="left:132px;top:2672px;width:227px;height:158px;background:linear-gradient(170deg,#d4d6d8,#6a6560)" role="img" aria-label="Instagram photo: covered boats"></div>
<div class="tile" style="left:369px;top:2355px;width:227px;height:158px;background:linear-gradient(170deg,#9aa0a4,#d8d4cc)" role="img" aria-label="Instagram photo: boat on stands"></div>
<div class="tile" style="left:369px;top:2521px;width:227px;height:309px;background:linear-gradient(170deg,#bcc2cc,#e6e8ec 60%,#d0d4da)" role="img" aria-label="Instagram photo: boat step with safety sticker"></div>
<div class="tile" style="left:605px;top:2355px;width:227px;height:309px;background:linear-gradient(160deg,#b86a34,#7a3a1a)" role="img" aria-label="Instagram photo: wooden cabinet with sticker"></div>
<div class="tile" style="left:605px;top:2672px;width:227px;height:158px;background:linear-gradient(160deg,#e8e8e8,#b8b8b8)" role="img" aria-label="Instagram photo: water container cap"></div>
<div class="tile" style="left:841px;top:2355px;width:227px;height:158px;background:linear-gradient(170deg,#6a7078,#3a3e44)" role="img" aria-label="Instagram photo: man on a boat ladder"></div>
<div class="tile" style="left:841px;top:2521px;width:227px;height:309px;background:linear-gradient(180deg,#c8a08a,#7a6058 50%,#3a3432)" role="img" aria-label="Instagram photo: angler fishing at sunset"></div>

<footer class="footer">
  <div class="brand"><span class="mark"></span>QUIBREL<br>OUTDOOR</div>
  <nav class="footlinks"><a>HOME</a><a>ABOUT US</a><a>SHOP</a><a>REVIEWS</a><a>BLOGS</a><a>CONTACT US</a></nav>
  <div class="social bottom">
    <span class="dot" aria-label="Share"><svg width="14" height="14" viewBox="0 0 24 24"><circle cx="18" cy="5" r="3" fill="#fff"/><circle cx="6" cy="12" r="3" fill="#fff"/><circle cx="18" cy="19" r="3" fill="#fff"/><path d="M8.6 10.5l6.8-4M8.6 13.5l6.8 4" stroke="#fff" stroke-width="2"/></svg></span>
    <span class="dot" aria-label="Email"><svg width="14" height="14" viewBox="0 0 24 24"><rect x="2" y="5" width="20" height="14" rx="2" fill="none" stroke="#fff" stroke-width="2.2"/><path d="M3 6l9 7 9-7" fill="none" stroke="#fff" stroke-width="2.2"/></svg></span>
    <span class="dot" aria-label="Chat"><svg width="14" height="14" viewBox="0 0 24 24"><path d="M4 4h16v11H9l-5 4z" fill="#fff"/></svg></span>
    <span class="dot" aria-label="Cart"><svg width="16" height="16" viewBox="0 0 24 24"><path d="M3 4h3l2 10h10l2-7H8" stroke="#fff" stroke-width="2" fill="none"/><circle cx="10" cy="19" r="1.8" fill="#fff"/><circle cx="17" cy="19" r="1.8" fill="#fff"/></svg></span>
  </div>
  <p class="copy">© COPYRIGHTS 2021 QUIBREL OUTDOOR &nbsp;|&nbsp;&nbsp; ALL RIGHTS RESERVED.</p>
</footer>

</body>
</html>
```